VORNAK SYSTEMS BUSINESS CARD DESIGN

WE WANT COMPLETE NEW DESIGN OF OUR BUSINESS CARD. WE ARE AN INTEGRATION COMPANY, WHERE WE INTEGRATE IOT/SMART SYSTEMS TO HOMES AND CORPORATE CUSTOMERS. WE SUPPLY AND INSTALL AUTOMATION PRODUCTS. THE FINAL DESIGN SHOULD COMMUNICATE TECHNOLOGY. THE CARD DESIGN SHOULD BE VERY IMPACT FULL. LOGO NEEDS TO BE THERE. IT WOULD NICE IF THE DESIGN WAS CLEAN. COLORS IS UP TO DESIGNER TO PLAY WITH, OR CAN STICK TO CORPORATE COLORS (FOLLOW LOGO). I HAVE ADDED FEW REFERENCE PHOTOS TO DRAW INSPIRATION MAYBE. I HAVE ADDED A HEX DESIGN, ITS NOT NECESSARY TO USE THIS DESIGN, ITS UPTO DESIGNER, JUST ADDED IF NEEDED TO PLAY WITH DESIGN.

Target Market(s)

Private end users and corporate clients

Industry/Entity Type

technology, home automation, home theaters, building management systems, IOT

Contact Information for Business Card

It should include Employee name, personal number, office number, email address, both in English and arabic. DETAILS TO INCLUDE :RAJESH PALLIVAL, MOBILE 0097150738265,OFFCIE 009714368547, RAJESH@VORNAKSYS.EXAMPLE

Requirements
Must have
• Should feel like a technology company from design. Details both and in English and arabic (or at least have provision for arabic in design).
Nice to have
• I would like logo on one side, and details on the other side. Logo design side should communicate technology with logo. Other side can be clean just with information or also have some design aspects following from logo side. it would be interesting to see submissions with square design as well (that looks like an app Icon). colors could be of logo, red black grey and white. I have added some designs to draw inspiration from

```html
<!DOCTYPE html>
<html lang="en">
<head>
<meta charset="utf-8">
<title>Vornak Systems Business Card</title>
<link href="https://fonts.googleapis.com/css2?family=Arimo:wght@400;700&family=Noto+Kufi+Arabic:wght@400;600&display=swap" rel="stylesheet">
<style>
  :root {
    --page: #161617;
    --card: #2e2e30;
    --card-deep: #1f1f21;
    --white: #f4f4f4;
    --grey: #a9a9ab;
    --red: #e0161e;
    --rule: #c9c9cb;
  }
  * { margin: 0; padding: 0; box-sizing: border-box; }
  html, body {
    width: 1200px; height: 963px; overflow: hidden;
    background: var(--page);
    font-family: "Arimo", Arial, sans-serif;
  }
  .sheet {
    width: 1200px; height: 963px;
    display: flex; flex-direction: column; align-items: center; justify-content: center;
    gap: 40px;
  }
  .card {
    position: relative;
    width: 760px; height: 434px;
    background: linear-gradient(160deg, #333335 0%, var(--card) 55%, #2a2a2c 100%);
    box-shadow: 0 14px 30px rgba(0,0,0,.55);
    overflow: hidden;
  }

  /* Brand block */
  .brand { position: absolute; display: flex; flex-direction: column; align-items: flex-start; z-index: 2; }
  .brand-row { display: flex; align-items: center; gap: 14px; }
  .brand-dot { width: 44px; height: 44px; border-radius: 50%; background: var(--red); flex: none; }
  .brand-name {
    font-weight: 700; color: var(--white);
    font-size: 42px; letter-spacing: 3px; line-height: 1;
  }
  .brand-sub {
    margin-top: 6px; margin-left: 58px;
    font-weight: 700; color: var(--grey); font-size: 16px; letter-spacing: 1px;
  }
  .brand-tagline {
    margin-top: 8px;
    color: var(--white); font-size: 13px; letter-spacing: 4px; font-weight: 400;
  }

  /* Details side */
  .details .brand { right: 52px; top: 118px; }
  .person { position: absolute; left: 56px; top: 250px; }
  .person-name {
    color: var(--red); font-size: 21px; letter-spacing: .5px; font-weight: 400; line-height: 1.2;
  }
  .person-role { color: var(--white); font-size: 16px; margin-top: 6px; line-height: 1.2; }
  .person-ar {
    position: absolute; right: 56px; top: 250px;
    direction: rtl; text-align: right;
    font-family: "Noto Kufi Arabic", sans-serif;
  }
  .person-ar .person-name { font-size: 18px; font-weight: 600; }
  .person-ar .person-role { font-size: 14px; margin-top: 4px; }
  .rule {
    position: absolute; left: 50px; right: 56px; top: 318px;
    height: 1px; background: var(--rule);
  }
  .contacts {
    position: absolute; left: 50px; right: 56px; top: 338px;
    display: flex; align-items: center; justify-content: space-between;
    color: var(--white); font-size: 15.5px; letter-spacing: .3px;
  }
  .contact { display: flex; align-items: center; gap: 8px; white-space: nowrap; }
  .contact svg { width: 15px; height: 15px; flex: none; }

  /* Brand side */
  .cover .brand { left: 48px; top: 42px; }
  .cover-emboss {
    position: absolute; left: 0; right: 0; bottom: 0; top: 150px;
    clip-path: polygon(0 38%, 100% 0, 100% 100%, 0 100%);
    background:
      radial-gradient(ellipse 60% 40% at 62% 88%, rgba(150,150,152,.45) 0%, rgba(150,150,152,0) 70%),
      linear-gradient(180deg, var(--card-deep) 0%, #262628 45%, #4a4a4c 80%, #3a3a3c 100%);
  }
</style>
</head>
<body>
<main class="sheet">

  <section class="card details" aria-label="Card details side">
    <div class="brand">
      <div class="brand-row">
        <span class="brand-dot"></span>
        <span class="brand-name">VORNAK</span>
      </div>
      <span class="brand-sub">SYSTEMS L.L.C</span>
      <span class="brand-tagline">A VORNAK GROUP DIVISION.</span>
    </div>

    <div class="person">
      <p class="person-name">RAJESH PALLIVAL</p>
      <p class="person-role">General Manager</p>
    </div>
    <div class="person-ar" lang="ar">
      <p class="person-name">راجيش باليفال</p>
      <p class="person-role">المدير العام</p>
    </div>
    <div class="rule"></div>

    <div class="contacts">
      <span class="contact">
        <svg viewBox="0 0 16 16" fill="none" stroke="var(--red)" stroke-width="1.5"><rect x="4" y="1" width="8" height="14" rx="1.5"/><line x1="7" y1="12.5" x2="9" y2="12.5"/></svg>
        0097150738265
      </span>
      <span class="contact">
        <svg viewBox="0 0 16 16" fill="var(--red)"><path d="M4 1.5l2.2 3-1.3 1.6c.8 1.9 2.2 3.4 4 4.3l1.6-1.3 3 2.2-1.2 2.5C7.4 13.6 2.4 8.6 1.5 3.7z"/></svg>
        009714368547
      </span>
      <span class="contact">
        <svg viewBox="0 0 16 16" fill="none" stroke="var(--red)" stroke-width="1.5"><rect x="1.5" y="3.5" width="13" height="9"/><polyline points="1.5,3.5 8,9 14.5,3.5"/></svg>
        RAJESH@VORNAKSYS.EXAMPLE
      </span>
    </div>
  </section>

  <section class="card cover" aria-label="Card brand side">
    <div class="brand">
      <div class="brand-row">
        <span class="brand-dot"></span>
        <span class="brand-name">VORNAK</span>
      </div>
      <span class="brand-sub">SYSTEMS L.L.C</span>
      <span class="brand-tagline">A VORNAK GROUP DIVISION.</span>
    </div>
    <div class="cover-emboss" role="img" aria-label="Large tone-on-tone embossed brand decoration with glossy grey highlights across the lower card"></div>
  </section>

</main>
</body>
</html>
```